Kestrel Facilities Business Card Design

We would now like to design business cards with the new Kestrel Facilities logo

Target Market(s)

Professional

Industry/Entity Type

Professional services

Contact Information for Business Card

Employee name, title, phone number, email address, corporate office address and logo.

Font styles to use
Sans Serif

Colors
0054AA
0677BA
7BADD7
CADEEF
E8F1F8

Requirements
Must have
• My logo
Should not have
• any other pictures or images besides my logo

```html
<!DOCTYPE html>
<html lang="en">
<head>
<meta charset="utf-8">
<title>Kestrel Facilities Business Card</title>
<link href="https://fonts.googleapis.com/css2?family=Open+Sans:wght@400;600;700&display=swap" rel="stylesheet">
<style>
  :root {
    --backdrop: #3b3b3b;
    --card: #1b1b1c;
    --blue: #3a7fd0;
    --white: #f2f2f2;
    --grey: #6a6a6c;
  }
  * { margin: 0; padding: 0; box-sizing: border-box; }
  html, body {
    width: 1200px; height: 801px; overflow: hidden;
    background: var(--backdrop);
    font-family: "Open Sans", Arial, sans-serif;
  }
  .stage {
    position: relative; width: 1200px; height: 801px;
    display: flex; align-items: center; justify-content: center; gap: 44px;
  }
  .card {
    position: relative; width: 520px; height: 296px;
    background: var(--card);
    border-bottom: 3px solid var(--blue);
    border-left: 3px solid var(--blue);
  }
  .front .brand {
    position: absolute; left: 40px; top: 70px;
    display: flex; align-items: center; gap: 12px;
  }
  .brand-square { width: 34px; height: 34px; background: var(--blue); }
  .brand-name {
    color: var(--blue); font-weight: 600; font-size: 22px; line-height: 1.05;
  }
  .front .divider {
    position: absolute; left: 112px; right: 26px; top: 182px;
    height: 1px; background: var(--blue);
  }
  .person {
    position: absolute; right: 26px; top: 138px; text-align: right;
  }
  .person-name {
    color: var(--blue); font-weight: 700; font-size: 19px; letter-spacing: 0.3px;
  }
  .person-title { color: var(--white); font-size: 11px; margin-top: -2px; }
  .address {
    position: absolute; right: 26px; top: 194px; text-align: right;
    color: var(--white); font-size: 12.5px; line-height: 1.45;
  }
  .contacts {
    position: absolute; left: 112px; top: 196px;
    list-style: none; color: var(--white); font-size: 12.5px; line-height: 1.55;
  }
  .contacts li { display: flex; align-items: center; gap: 8px; }
  .contacts svg { width: 10px; height: 10px; fill: var(--blue); flex: none; }
  .back .brand {
    position: absolute; left: 0; right: 0; top: 0; bottom: 0;
    display: flex; align-items: center; justify-content: center; gap: 16px;
  }
  .back .brand-square { width: 52px; height: 52px; background: var(--grey); }
  .back .brand-name { color: var(--grey); font-size: 34px; }
</style>
</head>
<body>
<main class="stage">
  <section class="card front">
    <div class="brand">
      <span class="brand-square"></span>
      <span class="brand-name">Kestrel<br>Facilities</span>
    </div>
    <div class="person">
      <p class="person-name">DANIEL REYES</p>
      <p class="person-title">CEO</p>
    </div>
    <div class="divider"></div>
    <p class="address">1480 Harbor Road<br>Westfield, MA 01085</p>
    <ul class="contacts">
      <li><svg viewBox="0 0 10 10"><path d="M2 0.5 L4 2.5 L3 3.8 Q4.5 6 6.2 7 L7.5 6 L9.5 8 L8 9.5 Q3 9 0.5 2 Z"/></svg>555-201-4837</li>
      <li><svg viewBox="0 0 10 10"><path d="M0 2 H10 V8 H0 Z M0.8 2.6 L5 5.6 L9.2 2.6 V2.4 H0.8 Z" fill-rule="evenodd"/></svg>dreyes@kestrelfacilities.com</li>
      <li><svg viewBox="0 0 10 10"><circle cx="5" cy="5" r="4.6"/></svg>www.kestrelfacilities.com</li>
    </ul>
  </section>
  <section class="card back">
    <div class="brand">
      <span class="brand-square"></span>
      <span class="brand-name">Kestrel Facilities</span>
    </div>
  </section>
</main>
</body>
</html>
```